Business cards to launch an education platform

Hi,
I am looking at having new business cards designed.
I am a startup, developing a web platform for schools and university, the education world. It's an online assessment system.
I would like a card that looks classy, and that is using the colors and the font of my logo.

I have attached:
1) my logo
2) A business card that I have designed quickly so you can have all the information required in the card, but I really don't like it.
3) The font that I am using (Lato Regular) to design my web platform
4) Some screenshots of my web platform so you can have a look at the style that I have.

Target Market(s)

Major market: Education system: Schools and university
Minor markets: Business in general

Industry/Entity Type

Business

Contact Information for Business Card

Clara Fenwick
Director

M: 0437 518 902
E: clara.fenwick@amberLoomSystems.com.au

Requirements
Must have
• The colors of my logo

```html
<!DOCTYPE html>
<html lang="en">
<head>
<meta charset="utf-8">
<title>Amber Loom Systems – Business Cards</title>
<link rel="stylesheet" href="https://fonts.googleapis.com/css2?family=Lato:wght@300;400;700&display=swap">
<style>
  :root {
    --navy: #0d4a80;
    --navy-deep: #0a3d6b;
    --sky: #35a8e0;
    --ink: #4a4f55;
    --rule: #d5dbe1;
    --paper: #ffffff;
    --backdrop: #eceef1;
  }
  * { margin: 0; padding: 0; box-sizing: border-box; }
  html, body {
    width: 1200px; height: 950px; overflow: hidden;
    background: var(--backdrop);
    font-family: "Lato", Arial, sans-serif;
  }
  .canvas { position: relative; width: 1200px; height: 950px; }

  .card {
    position: absolute;
    width: 740px; height: 423px;
    border-radius: 4px;
    overflow: hidden;
    box-shadow: 0 6px 18px rgba(0,0,0,0.12);
  }

  /* Back of card */
  .card-back {
    left: 80px; top: 40px;
    background: linear-gradient(135deg, var(--navy) 0%, var(--navy-deep) 100%);
    color: var(--paper);
  }
  .card-back .brand {
    position: absolute; left: 0; right: 0; top: 110px;
    display: flex; flex-direction: column; align-items: center; gap: 16px;
  }
  .card-back .brand-mark { width: 50px; height: 50px; background: var(--paper); }
  .card-back .brand-name {
    font-size: 34px; font-weight: 400; letter-spacing: 1px; color: var(--paper);
    line-height: 1.1; text-align: center;
  }
  .card-back .website {
    position: absolute; left: 0; right: 0; bottom: 62px;
    text-align: center; font-size: 17px; letter-spacing: 2.5px; font-weight: 400;
  }

  /* Front of card */
  .card-front {
    left: 380px; top: 487px;
    background: var(--paper);
  }
  .card-front .brand {
    position: absolute; left: 40px; top: 150px; width: 250px;
    display: flex; flex-direction: column; align-items: center; gap: 12px;
  }
  .card-front .brand-mark { width: 40px; height: 40px; background: var(--navy); }
  .card-front .brand-name {
    font-size: 24px; font-weight: 400; color: var(--navy); letter-spacing: 0.5px;
    line-height: 1.15; text-align: center;
  }
  .card-front .divider {
    position: absolute; left: 318px; top: 80px;
    width: 1px; height: 200px; background: var(--rule);
  }
  .contact { position: absolute; left: 344px; top: 92px; }
  .contact .person-name { font-size: 26px; font-weight: 700; color: var(--navy); }
  .contact .person-role { font-size: 17px; font-weight: 400; color: var(--sky); margin-top: 4px; }
  .contact .line {
    display: flex; align-items: center; gap: 10px;
    font-size: 17px; color: var(--ink); margin-top: 14px; white-space: nowrap;
  }
  .contact .line:first-of-type { margin-top: 36px; }
  .contact .icon { width: 18px; height: 18px; flex: none; }

  .card-front .accent-line {
    position: absolute; left: 0; right: 0; top: 352px; height: 4px; background: var(--sky);
  }
  .card-front .footer-band {
    position: absolute; left: 0; right: 0; top: 362px; bottom: 0;
    background: linear-gradient(90deg, var(--navy-deep), var(--navy));
  }
</style>
</head>
<body>
<main class="canvas">

  <section class="card card-back" aria-label="Card back">
    <div class="brand">
      <span class="brand-mark"></span>
      <span class="brand-name">Amber Loom<br>Systems</span>
    </div>
    <p class="website">www.amberLoomSystems.com.au</p>
  </section>

  <section class="card card-front" aria-label="Card front">
    <div class="brand">
      <span class="brand-mark"></span>
      <span class="brand-name">Amber Loom<br>Systems</span>
    </div>
    <div class="divider"></div>
    <div class="contact">
      <p class="person-name">Clara Fenwick</p>
      <p class="person-role">Director</p>
      <p class="line">
        <svg class="icon" viewBox="0 0 18 18" aria-hidden="true">
          <rect x="4.5" y="1" width="9" height="16" rx="1.5" fill="none" stroke="#0d4a80" stroke-width="1.6"/>
          <line x1="7.5" y1="14" x2="10.5" y2="14" stroke="#0d4a80" stroke-width="1.4"/>
        </svg>
        0437 518 902
      </p>
      <p class="line">
        <svg class="icon" viewBox="0 0 18 18" aria-hidden="true">
          <rect x="1.5" y="4" width="15" height="10" fill="#0d4a80"/>
          <polyline points="1.5,4 9,10 16.5,4" fill="none" stroke="#ffffff" stroke-width="1.3"/>
        </svg>
        clara.fenwick@amberLoomSystems.com.au
      </p>
    </div>
    <div class="accent-line"></div>
    <div class="footer-band"></div>
  </section>

</main>
</body>
</html>
```